Harbor Ridge Painting Epoxy Flyer

We need a promotional flyer for a new epoxy floor coatings division of our painting company. We do epoxy garage floor coatings and paver sealing. It needs to be based on and very similar to the attached flyer. The garage floor picture needs to look more realistic, and the before and after pavers pictures should look less shiny but still a good contrast. Include attached logo

```html
<!DOCTYPE html>
<html lang="en">
<head>
<meta charset="utf-8">
<title>Harbor Ridge Painting – Garage &amp; Driveway Flyer</title>
<link href="https://fonts.googleapis.com/css2?family=Anton&family=Oswald:wght@500;600&family=Poppins:wght@500;600;700&display=swap" rel="stylesheet">
<style>
  :root {
    --backdrop: #c0c0c0;
    --paper: #ffffff;
    --ink: #0a0a0a;
    --night: #000000;
    --blue: #2a8ad8;
    --teal: #2fa08a;
    --green: #52a825;
    --orange: #c8650a;
    --text-light: #ffffff;
  }
  * { box-sizing: border-box; margin: 0; padding: 0; }
  html, body { width: 904px; height: 1200px; overflow: hidden; background: var(--backdrop); }
  .stage {
    position: relative; width: 1666px; height: 2212px;
    transform: scale(0.54262); transform-origin: 0 0;
  }
  .flyer {
    position: absolute; left: 252px; top: 234px; width: 1162px; height: 1743px;
    background: var(--paper); overflow: hidden;
  }
  .dark-band { position: absolute; left: 0; top: 654px; width: 100%; height: 934px; background: var(--night); }
  .art { position: absolute; left: 0; top: 0; width: 1162px; height: 1743px; }
  .abs { position: absolute; white-space: nowrap; line-height: 1; }

  .brand { left: 70px; top: 124px; width: 340px; display: flex; align-items: center; gap: 16px; }
  .brand-dot { flex: none; width: 44px; height: 44px; border-radius: 50%; background: var(--teal); }
  .brand-name { font-family: "Poppins", sans-serif; font-weight: 600; font-size: 30px; line-height: 1.15; color: var(--ink); text-transform: uppercase; letter-spacing: 0.5px; }

  .headline-1 { left: 458px; top: 22px; font-family: "Anton", sans-serif; font-size: 118px; color: var(--ink); }
  .headline-2 { left: 458px; top: 140px; font-family: "Anton", sans-serif; font-size: 86px; color: var(--ink); }
  .subhead { left: 460px; top: 240px; font-family: "Poppins", sans-serif; font-weight: 600; font-size: 39px; color: var(--ink); letter-spacing: 0.3px; }

  .photo-label { font-family: "Anton", sans-serif; color: var(--text-light); transform: translateX(-50%); }
  .photo-label--big { font-size: 44px; top: 396px; }
  .photo-label--small { font-size: 20px; top: 777px; }

  .service-title { font-family: "Oswald", sans-serif; font-weight: 600; font-size: 42px; color: var(--text-light); transform: translateX(-50%); top: 1096px; }
  .benefits { position: absolute; list-style: none; font-family: "Poppins", sans-serif; font-weight: 500; font-size: 23px; color: var(--text-light); line-height: 27px; }
  .benefits li { position: relative; padding-left: 30px; margin-bottom: 18px; }
  .benefits li::before {
    content: "✓"; position: absolute; left: 0; top: 5px; width: 18px; height: 18px; border-radius: 50%;
    font-size: 12px; line-height: 18px; text-align: center; font-weight: 700;
  }
  .benefits--epoxy { left: 162px; top: 1168px; }
  .benefits--epoxy li::before { background: var(--blue); }
  .benefits--paver { left: 629px; top: 1168px; }
  .benefits--paver li::before { background: var(--green); }

  .tagline { left: 50%; top: 1408px; transform: translateX(-50%); font-family: "Oswald", sans-serif; font-weight: 600; font-size: 42px; color: var(--text-light); }
  .trust { font-family: "Oswald", sans-serif; font-weight: 600; font-size: 34px; line-height: 40px; color: var(--text-light); top: 1480px; white-space: nowrap; }

  .cta-small { left: 83px; top: 1610px; font-family: "Anton", sans-serif; font-size: 48px; color: var(--ink); }
  .cta-big { left: 81px; top: 1656px; font-family: "Anton", sans-serif; font-size: 82px; color: var(--ink); }
  .phone-number { left: 516px; top: 1606px; font-family: "Poppins", sans-serif; font-weight: 600; font-size: 76px; color: var(--ink); letter-spacing: 1px; }
  .phone-sub { left: 434px; top: 1690px; font-family: "Poppins", sans-serif; font-weight: 600; font-size: 29px; color: var(--ink); }
</style>
</head>
<body>
<div class="stage">
  <div class="flyer">
    <div class="dark-band"></div>

    <svg class="art" viewBox="0 0 1162 1743" xmlns="http://www.w3.org/2000/svg">
      <defs>
        <linearGradient id="ringGrad" x1="0" y1="0" x2="0" y2="1">
          <stop offset="0" stop-color="#2a8ad8"/>
          <stop offset="0.3" stop-color="#2fa08a"/>
          <stop offset="0.55" stop-color="#52a825"/>
          <stop offset="1" stop-color="#c8650a"/>
        </linearGradient>
        <linearGradient id="frameGrad" x1="0" y1="0" x2="0" y2="1">
          <stop offset="0" stop-color="#2a8ad8"/>
          <stop offset="0.5" stop-color="#52a825"/>
          <stop offset="1" stop-color="#c8650a"/>
        </linearGradient>
        <linearGradient id="paverBefore" x1="0" y1="0" x2="0" y2="1">
          <stop offset="0" stop-color="#7b8a6a"/>
          <stop offset="0.3" stop-color="#6f7174"/>
          <stop offset="1" stop-color="#595b5e"/>
        </linearGradient>
        <linearGradient id="paverAfter" x1="0" y1="0" x2="0" y2="1">
          <stop offset="0" stop-color="#8e9a80"/>
          <stop offset="0.3" stop-color="#b9bcbf"/>
          <stop offset="1" stop-color="#9d9fa2"/>
        </linearGradient>
        <linearGradient id="floorBefore" x1="0" y1="0" x2="0" y2="1">
          <stop offset="0" stop-color="#4a4440"/>
          <stop offset="0.35" stop-color="#e4e6e8"/>
          <stop offset="1" stop-color="#cfd2d5"/>
        </linearGradient>
        <linearGradient id="floorAfter" x1="0" y1="0" x2="0" y2="1">
          <stop offset="0" stop-color="#3a3836"/>
          <stop offset="0.35" stop-color="#f0f0f0"/>
          <stop offset="0.5" stop-color="#b2b4b6"/>
          <stop offset="1" stop-color="#9fa1a3"/>
        </linearGradient>
        <clipPath id="bigPhoto"><circle cx="505" cy="691" r="329"/></clipPath>
        <clipPath id="smallPhoto"><circle cx="836" cy="801" r="193"/></clipPath>
      </defs>

      <path d="M 858 561 A 372 372 0 1 0 693 1012" fill="none" stroke="url(#ringGrad)" stroke-width="26"/>

      <circle cx="505" cy="691" r="345" fill="#ffffff"/>
      <g clip-path="url(#bigPhoto)">
        <rect x="170" y="360" width="340" height="670" fill="url(#paverBefore)" role="img" aria-label="Paver driveway before sealing"/>
        <rect x="510" y="360" width="330" height="670" fill="url(#paverAfter)" role="img" aria-label="Paver driveway after sealing"/>
        <rect x="170" y="360" width="670" height="120" fill="#52a825"/>
        <rect x="507" y="360" width="5" height="670" fill="#ffffff"/>
      </g>

      <circle cx="836" cy="801" r="218" fill="#ffffff"/>
      <g clip-path="url(#smallPhoto)">
        <rect x="640" y="600" width="193" height="400" fill="url(#floorBefore)" role="img" aria-label="Garage floor before epoxy coating"/>
        <rect x="833" y="600" width="200" height="400" fill="url(#floorAfter)" role="img" aria-label="Garage floor after epoxy coating"/>
        <rect x="828" y="600" width="10" height="400" fill="#ffffff"/>
      </g>
      <rect x="706" y="772" width="122" height="30" fill="#52a825"/>
      <rect x="838" y="772" width="128" height="30" fill="#52a825"/>

      <rect x="106" y="1122" width="452" height="264" rx="20" fill="none" stroke="url(#frameGrad)" stroke-width="3"/>
      <rect x="606" y="1122" width="451" height="264" rx="20" fill="none" stroke="url(#frameGrad)" stroke-width="3"/>
      <rect x="135" y="1096" width="393" height="55" rx="27.5" fill="#2a8ad8"/>
      <rect x="635" y="1096" width="393" height="55" rx="27.5" fill="#52a825"/>

      <g fill="none" stroke="url(#ringGrad)" stroke-width="2.5">
        <circle cx="128" cy="1519" r="42"/>
        <circle cx="434" cy="1519" r="42"/>
        <circle cx="777" cy="1519" r="42"/>
      </g>
      <g>
        <path d="M128 1494 l20 8 v14 c0 12 -9 20 -20 25 c-11 -5 -20 -13 -20 -25 v-14 z" fill="#2fa08a"/>
        <path d="M117 1517 l8 8 l15 -16" fill="none" stroke="#ffffff" stroke-width="4"/>
        <path d="M434 1496 l18 7 v13 c0 11 -8 18 -18 23 c-10 -5 -18 -12 -18 -23 v-13 z" fill="#2a8ad8"/>
        <path d="M426 1517 l6 6 l11 -12" fill="none" stroke="#ffffff" stroke-width="3.5"/>
        <rect x="440" y="1522" width="16" height="16" rx="3" fill="#e0a020"/>
        <path d="M777 1495 c-10 0 -17 7 -17 16 c0 12 17 26 17 26 c0 0 17 -14 17 -26 c0 -9 -7 -16 -17 -16 z" fill="#52a825"/>
        <circle cx="777" cy="1511" r="6" fill="#000000"/>
        <ellipse cx="777" cy="1540" rx="20" ry="6" fill="none" stroke="#c8650a" stroke-width="2.5"/>
      </g>

      <circle cx="466" cy="1646" r="33" fill="url(#ringGrad)"/>
      <path d="M455 1632 c3 -2 6 -1 7 2 l3 6 c1 2 0 4 -2 5 l-2 2 c2 5 6 9 11 11 l2 -2 c1 -2 3 -3 5 -2 l6 3 c3 1 4 4 2 7 l-3 3 c-3 3 -8 3 -13 1 c-9 -4 -16 -11 -20 -20 c-2 -5 -2 -10 1 -13 z" fill="#ffffff"/>
    </svg>

    <div class="abs brand"><span class="brand-dot"></span><span class="brand-name">Harbor Ridge<br>Painting</span></div>

    <h1 class="abs headline-1">Upgrade Your</h1>
    <div class="abs headline-2">Garage &amp; Driveway</div>
    <p class="abs subhead">FROM WORN-OUT TO LIKE NEW</p>

    <span class="abs photo-label photo-label--big" style="left:408px">Before</span>
    <span class="abs photo-label photo-label--big" style="left:614px">After</span>
    <span class="abs photo-label photo-label--small" style="left:767px">Before</span>
    <span class="abs photo-label photo-label--small" style="left:901px">After</span>

    <h2 class="abs service-title" style="left:331px">Epoxy Floor Coatings</h2>
    <ul class="benefits benefits--epoxy">
      <li>Durable, long-lasting finish</li>
      <li>Slip-resistant texture</li>
      <li>Covers cracks &amp;<br>imperfections</li>
      <li>Easy to clean &amp; maintain</li>
    </ul>

    <h2 class="abs service-title" style="left:831px">Paver Sealing</h2>
    <ul class="benefits benefits--paver">
      <li>Restores color &amp; enhances<br>appearance</li>
      <li>Protects from sun fading</li>
      <li>Helps prevent weeds &amp; sand loss</li>
      <li>Easier to clean &amp; maintain</li>
    </ul>

    <p class="abs tagline">Practical upgrades that protect and improve your home</p>

    <p class="abs trust" style="left:194px">Licensed &amp;<br>Insured</p>
    <p class="abs trust" style="left:500px">Family-Owned<br>Local Business</p>
    <p class="abs trust" style="left:843px">Serving Prescott &amp;<br>Surrounding Areas</p>

    <p class="abs cta-small">CALL FOR A FREE</p>
    <p class="abs cta-big">ESTIMATE</p>
    <p class="abs phone-number">928-555-0147</p>
    <p class="abs phone-sub">Fast, professional service you can trust</p>
  </div>
</div>
</body>
</html>
```